Business Cards Design for the electrical wholesaler: clean bold dynamic :)

We need a business card design that would follow our latest brand guidelines. As an electrical wholesaler we want to bring a fresh look and feel into the industry. The design should be clean bold and dynamic. It should come alive with the renewed energy of our green colour. Our grey colour should keep things balanced and complement the notion of maturity and responsibility. We employ Lato as a corporate font however are not bound by this font and we’re open to interpretation here.

Target Market(s)

Electrical contractors

Industry/Entity Type

Business

Contact Information for Business Card

Logo
Name & Surname: Halyna Dorosh
Job Title: Director of Marketing
Email: halya.dorosh@quillmail.example
Cell phone: 780.555.0137
Address: 20517 - 87 Ave. Edmonton, AB, Canada. T6K 4N8
Business Phone: 780.555.0184
Website: www.brovix.example

Font styles to use
Other font styles liked:
• Lato

Requirements
Must have
• Logo & website
Nice to have
• Brand elements - some of them you may find in the attached Brand Guidelines (e.g. three lines on the background signifying "W")

```html
<!DOCTYPE html>
<html lang="en">
<head>
<meta charset="utf-8">
<title>Brovix business card</title>
<link rel="stylesheet" href="https://fonts.googleapis.com/css2?family=Lato:ital,wght@0,300;0,400;0,700;1,700&display=swap">
<style>
  :root {
    --backdrop: #3a3a3b;
    --card: #232324;
    --green: #7dc226;
    --grey: #bdbdbd;
    --band: #5b5b5d;
    --white: #ffffff;
  }
  * { box-sizing: border-box; margin: 0; padding: 0; }
  html, body { width: 799px; height: 1200px; overflow: hidden; }
  body {
    background: var(--backdrop);
    font-family: "Lato", sans-serif;
    position: relative;
  }
  .card {
    position: absolute;
    left: 90px;
    width: 620px;
    height: 354px;
    background: var(--card);
    border-radius: 24px;
    overflow: hidden;
  }
  .card--front { top: 140px; }
  .card--back { top: 700px; }

  .wordmark { position: absolute; display: flex; flex-direction: column; }
  .wordmark__row { display: flex; align-items: center; gap: 14px; }
  .wordmark__square { width: 40px; height: 40px; background: var(--green); border-radius: 4px; }
  .wordmark__name { font-weight: 400; color: var(--grey); line-height: 1; }
  .wordmark__tagline {
    color: var(--green); font-weight: 700; letter-spacing: 2px;
    text-transform: uppercase;
  }
  .card--front .wordmark { left: 150px; top: 130px; }
  .card--front .wordmark__name { font-size: 78px; }
  .card--front .wordmark__tagline { font-size: 13px; margin: 6px 0 0 54px; }

  .card--back .wordmark { right: 40px; top: 108px; align-items: flex-end; }
  .card--back .wordmark__square { width: 28px; height: 28px; }
  .card--back .wordmark__name { font-size: 54px; }
  .card--back .wordmark__tagline { font-size: 9.5px; margin-top: 4px; }

  .accent-dot {
    position: absolute; left: -22px; top: 20px;
    width: 44px; height: 44px; border-radius: 50%; background: var(--green);
  }
  .person { position: absolute; left: 42px; top: 22px; }
  .person__name { color: var(--green); font-weight: 700; font-style: italic; font-size: 24px; }
  .person__title { color: var(--white); font-size: 12px; margin-top: 2px; }

  .contacts { position: absolute; left: 42px; top: 90px; list-style: none; }
  .contacts li {
    display: flex; align-items: center; gap: 10px;
    color: var(--white); font-size: 13px; line-height: 19px;
  }
  .contacts svg { width: 12px; height: 12px; flex: none; }

  .wave { position: absolute; left: 0; top: 0; width: 620px; height: 354px; }
  .address {
    position: absolute; right: 40px; bottom: 26px;
    color: var(--white); font-size: 16px; text-align: right; line-height: 1.35;
  }
</style>
</head>
<body>
  <section class="card card--front" aria-label="Card front">
    <div class="wordmark">
      <div class="wordmark__row">
        <span class="wordmark__square"></span>
        <span class="wordmark__name">brovix</span>
      </div>
      <span class="wordmark__tagline">Electrical Wholesalers</span>
    </div>
  </section>

  <section class="card card--back" aria-label="Card back">
    <svg class="wave" viewBox="0 0 620 354" aria-hidden="true">
      <path d="M0,172 C160,200 330,310 620,215 L620,238 C330,328 160,222 0,198 Z" fill="var(--band)"/>
      <path d="M0,210 C160,232 330,338 620,250 L620,354 L0,354 Z" fill="var(--green)"/>
    </svg>
    <span class="accent-dot"></span>
    <div class="person">
      <p class="person__name">Halyna Dorosh</p>
      <p class="person__title">Director of Marketing</p>
    </div>
    <ul class="contacts">
      <li>
        <svg viewBox="0 0 12 12"><circle cx="6" cy="6" r="6" fill="var(--green)"/><path d="M3.5 3h1.5l.6 1.6-.8.6a4 4 0 0 0 1.9 1.9l.6-.8 1.6.6V8.5a.8.8 0 0 1-.8.7A5.5 5.5 0 0 1 3 3.8a.8.8 0 0 1 .5-.8z" fill="var(--card)"/></svg>
        780.555.0184
      </li>
      <li>
        <svg viewBox="0 0 12 12"><circle cx="6" cy="6" r="6" fill="var(--green)"/><rect x="4.2" y="2.6" width="3.6" height="6.8" rx="0.6" fill="none" stroke="var(--card)" stroke-width="0.9"/><circle cx="6" cy="8.2" r="0.4" fill="var(--card)"/></svg>
        780.555.0137
      </li>
      <li>
        <svg viewBox="0 0 12 12"><circle cx="6" cy="6" r="6" fill="var(--green)"/><rect x="3" y="4" width="6" height="4" fill="none" stroke="var(--card)" stroke-width="0.9"/><path d="M3 4l3 2.2L9 4" fill="none" stroke="var(--card)" stroke-width="0.9"/></svg>
        halya.dorosh@quillmail.example
      </li>
      <li>
        <svg viewBox="0 0 12 12"><circle cx="6" cy="6" r="6" fill="var(--green)"/><circle cx="6" cy="6" r="3" fill="none" stroke="var(--card)" stroke-width="0.9"/><path d="M3 6h6M6 3v6" stroke="var(--card)" stroke-width="0.7"/></svg>
        www.brovix.example
      </li>
    </ul>
    <div class="wordmark">
      <div class="wordmark__row">
        <span class="wordmark__square"></span>
        <span class="wordmark__name">brovix</span>
      </div>
      <span class="wordmark__tagline">Electrical Wholesalers</span>
    </div>
    <p class="address">20517 - 87 Ave.<br>Edmonton, AB, Canada T6K 4N8</p>
  </section>
</body>
</html>
```